Business Card Design

We need a business card designed for our new company. Prefer a black card with white logo & writing.

Contact Information for Business Card

Ted Galloway, address: 7-4812 Fernhollow Road, Abbotsford, BC, V3K 8R2, Office Phone: 604-712-3390, Cell: 604-947-2164, Email: ted@resinworkshub.ca

Colors

Designer to choose only greyscale colors for use in the design.

```html
<!DOCTYPE html>
<html lang="en">
<head>
<meta charset="utf-8">
<title>Resin Works Hub – Business Card</title>
<link href="https://fonts.googleapis.com/css2?family=Poppins:wght@300;400;600;700&display=swap" rel="stylesheet">
<style>
  :root {
    --backdrop: #2b2b2d;
    --card: #1f1f22;
    --card-light: #2a2a2e;
    --ink: #ffffff;
    --ink-soft: #d9d9d9;
    --rule: #8a8a8a;
  }
  * { box-sizing: border-box; margin: 0; padding: 0; }
  html, body {
    width: 1200px; height: 711px; overflow: hidden;
    background: var(--backdrop);
    font-family: "Poppins", sans-serif;
    color: var(--ink);
  }
  .stage { position: relative; width: 1200px; height: 711px; }
  .card {
    position: absolute; top: 201px;
    width: 540px; height: 309px;
    background: var(--card);
    box-shadow: 0 12px 30px rgba(0,0,0,.55);
    overflow: hidden;
  }
  .card--front { left: 45px; }
  .card--back { left: 615px; }
  .edge-bar { position: absolute; width: 14px; background: var(--ink); }
  .edge-bar--right { right: 0; top: 34px; height: 110px; }
  .edge-bar--left { left: 0; bottom: 30px; height: 110px; }

  .pattern-field {
    position: absolute; inset: 0;
    background: linear-gradient(135deg, var(--card-light) 0%, var(--card) 60%, #19191b 100%);
  }
  .brand {
    position: absolute; display: flex; align-items: center; gap: 10px;
    font-weight: 700; color: var(--ink); letter-spacing: 1px;
  }
  .brand__mark { width: 14px; height: 14px; background: var(--ink); flex: none; }
  .card--front .brand {
    left: 50%; top: 50%; transform: translate(-50%, -50%);
    font-size: 34px; white-space: nowrap;
  }
  .card--back .brand {
    left: 36px; top: 112px; width: 180px;
    font-size: 21px; line-height: 1.15;
  }
  .card--back .brand__mark { width: 12px; height: 12px; }

  .divider {
    position: absolute; left: 232px; top: 70px; width: 1px; height: 150px;
    background: var(--rule);
  }
  .contact { position: absolute; left: 262px; top: 66px; }
  .contact__name { font-size: 26px; line-height: 1.1; font-weight: 300; }
  .contact__name strong { font-weight: 700; }
  .contact__role { font-size: 13px; font-weight: 300; color: var(--ink-soft); margin-bottom: 12px; }
  .contact__list { list-style: none; }
  .contact__item {
    display: flex; align-items: center; gap: 9px;
    font-size: 13px; font-weight: 300; line-height: 22px;
  }
  .contact__item svg { width: 13px; height: 13px; flex: none; }
  .address {
    position: absolute; left: 0; right: 0; bottom: 30px;
    text-align: center; font-size: 14px; font-weight: 400;
  }
</style>
</head>
<body>
<main class="stage">
  <section class="card card--front">
    <div class="pattern-field" role="img" aria-label="Repeating pattern of small company emblems on a dark background"></div>
    <div class="edge-bar edge-bar--right"></div>
    <div class="edge-bar edge-bar--left"></div>
    <div class="brand"><span class="brand__mark"></span>RESIN WORKS HUB</div>
  </section>

  <section class="card card--back">
    <div class="edge-bar edge-bar--right"></div>
    <div class="edge-bar edge-bar--left"></div>
    <div class="brand"><span class="brand__mark"></span><span class="brand__name">RESIN WORKS<br>HUB</span></div>
    <div class="divider"></div>
    <div class="contact">
      <h1 class="contact__name"><strong>Ted</strong> Galloway</h1>
      <p class="contact__role">Founder &amp; CEO</p>
      <ul class="contact__list">
        <li class="contact__item">
          <svg viewBox="0 0 24 24" fill="none" stroke="#fff" stroke-width="2"><path d="M5 3h4l2 5-3 2a11 11 0 0 0 6 6l2-3 5 2v4a2 2 0 0 1-2 2A17 17 0 0 1 3 5a2 2 0 0 1 2-2z"/></svg>
          604-712-3390
        </li>
        <li class="contact__item">
          <svg viewBox="0 0 24 24" fill="none" stroke="#fff" stroke-width="2"><rect x="6" y="2" width="12" height="20" rx="2"/><line x1="11" y1="18" x2="13" y2="18"/></svg>
          604-947-2164
        </li>
        <li class="contact__item">
          <svg viewBox="0 0 24 24" fill="none" stroke="#fff" stroke-width="2"><circle cx="12" cy="12" r="10"/><path d="M2 12h20M12 2a15 15 0 0 1 0 20M12 2a15 15 0 0 0 0 20"/></svg>
          www.resinworkshub.ca
        </li>
        <li class="contact__item">
          <svg viewBox="0 0 24 24" fill="none" stroke="#fff" stroke-width="2"><rect x="2" y="5" width="20" height="14" rx="1"/><path d="M2 6l10 7 10-7"/></svg>
          ted@resinworkshub.ca
        </li>
      </ul>
    </div>
    <p class="address">7-4812 Fernhollow Road, Abbotsford, BC, V3K 8R2.</p>
  </section>
</main>
</body>
</html>
```